Dental Practice Billboard Design

We are a newer dental practice in need of a simple but appealing billboard for our growing dental practice to attract new patients. The practice is owned by husband and wife dentists and is family friendly in a small town in Kentucky. We try to be very friendly and caring to our patients. Would prefer a blue background for the billboard and our tooth logo to be prominent. We are partial to the Patua One font used in the image below but please feel free to tweak it as you deem necessary. The shape of the uppercase D and lowercase g are why we like that font, so fonts with a similarly shaped “D” and “g” would work as well. Please include our phone number (555) 847-1390. Please see our website Harlowbrookdentistry.example for more info on the practice if needed. Thank you! Looking forward to seeing your creation.
Updates

The dimensions will be 12ft x 24ft (3.6576m x 7.3152m). Apologies for not including this in the original prompt. Thank you all for your submissions.

Industry/Entity Type

Dental

Font styles to use
Other font styles liked:
• Patua One

Colors
0054AA
0677BA
7BADD7
CADEEF
E8F1F8
0094D4
00A9DD
6FCCEA
C7EBF8
E9F6FB
00AB8E
00BBA5
67D7C9
C6EFE9
E9F9F6
59FF00
82FF00
B8FF75
E3FFCB
F4FFEA

Requirements
Must have
• Phone number, website, Logo, Practice name “Harlow Brook Dentistry”
Should not have
• A tagline or slogan

```html
<!DOCTYPE html>
<html lang="en">
<head>
<meta charset="utf-8">
<title>Harlow Brook Dentistry – Billboard</title>
<link href="https://fonts.googleapis.com/css2?family=Patua+One&family=Roboto+Condensed:wght@700&display=swap" rel="stylesheet">
<style>
  :root {
    --page-bg: #ffffff;
    --brand-blue-deep: #06307f;
    --brand-blue-light: #1f5bc0;
    --logo-blue: #0054aa;
    --leaf-green: #1fae1c;
    --leaf-green-light: #3cc42e;
    --forest-green: #0b5e14;
    --white: #ffffff;
    --photo-warm: #c9a48c;
    --photo-cool: #dfe8ef;
  }
  * { margin: 0; padding: 0; box-sizing: border-box; }
  html, body {
    width: 1102px; height: 1200px; overflow: hidden;
    background: var(--page-bg);
  }
  .billboard {
    position: absolute; left: 31px; top: 447px;
    width: 1040px; height: 306px;
    background: var(--white);
    box-shadow: 0 6px 18px rgba(0,0,0,0.25);
    overflow: hidden;
    font-family: "Patua One", Georgia, serif;
  }
  .billboard-shapes { position: absolute; inset: 0; }
  .practice-name {
    position: absolute; left: 64px; top: 22px;
    display: flex; align-items: center; gap: 10px;
    color: var(--logo-blue); font-size: 20px; line-height: 22px;
  }
  .practice-name .mark {
    flex: none; width: 34px; height: 34px; border-radius: 50%;
    background: var(--leaf-green);
  }
  .headline-pill {
    position: absolute; left: 340px; top: 46px;
    width: 662px; height: 52px; border-radius: 26px;
    background: linear-gradient(180deg, var(--leaf-green-light), var(--leaf-green));
    color: var(--white); font-size: 32px; line-height: 52px;
    text-align: center; white-space: nowrap;
  }
  .headline-main {
    position: absolute; left: 340px; top: 100px; width: 662px;
    color: var(--white); font-size: 78px; line-height: 100px;
    text-align: center; white-space: nowrap;
    text-shadow: 0 2px 4px rgba(0,0,0,0.25);
  }
  .contact-pill {
    position: absolute; left: 340px; top: 212px;
    width: 674px; height: 53px; border-radius: 27px;
    background: var(--leaf-green);
    box-shadow: 0 5px 6px -3px rgba(0,0,0,0.45);
    display: flex; overflow: hidden;
  }
  .contact-phone {
    width: 322px; height: 100%;
    background: var(--forest-green);
    border-radius: 27px;
    color: var(--white);
    font-family: "Roboto Condensed", Arial, sans-serif; font-weight: 700;
    font-size: 40px; line-height: 53px; text-align: center;
  }
  .contact-web {
    flex: 1; color: var(--white); font-size: 21px;
    line-height: 53px; text-align: center; white-space: nowrap;
  }
</style>
</head>
<body>
  <section class="billboard">
    <svg class="billboard-shapes" width="1040" height="306" viewBox="0 0 1040 306">
      <defs>
        <linearGradient id="photoTone" x1="0" y1="0" x2="1" y2="1">
          <stop offset="0" stop-color="var(--photo-cool)"/>
          <stop offset="0.6" stop-color="var(--photo-warm)"/>
          <stop offset="1" stop-color="var(--photo-cool)"/>
        </linearGradient>
        <linearGradient id="panelBlue" x1="0" y1="0" x2="0" y2="1">
          <stop offset="0" stop-color="var(--brand-blue-light)"/>
          <stop offset="1" stop-color="var(--brand-blue-deep)"/>
        </linearGradient>
      </defs>
      <rect class="family-photo" x="0" y="88" width="350" height="218" fill="url(#photoTone)" role="img" aria-label="Photo of a smiling family of four seated together in a bright dental office"/>
      <path class="blue-panel" d="M330 0 H1040 V235 H360 Q392 110 330 0 Z" fill="url(#panelBlue)"/>
      <path class="green-arc" d="M272 0 L330 0 Q396 120 352 306 L338 306 Q372 120 272 0 Z" fill="var(--leaf-green)"/>
    </svg>

    <div class="practice-name"><span class="mark"></span><span>Harlow Brook<br>Dentistry</span></div>

    <div class="headline-pill">HARLOW BROOK</div>
    <div class="headline-main">DENTISTRY</div>

    <div class="contact-pill">
      <div class="contact-phone">(555) 847-1390</div>
      <div class="contact-web">Harlowbrookdentistry.example</div>
    </div>
  </section>
</body>
</html>
```